Business Card for beauty technology startup

Design Glimora Business Card for a Beauty, based on the website identity and colors (https://www.glimora-example.com).
Glimora is a beauty tech startup that gathers helpful product info for beauty lovers and consumers (such as availability on stores, price range and product reviews) for makeup products. The card design must be young, colorful but clean, and very modern.

Target Market(s)

woman, 15-35

Industry/Entity Type

Cosmetics

Contact Information for Business Card

Full Name, address, phone

Font styles to use
Other font styles liked:
• Advent Pro

Colors
e34297
86cfc6
ffffff
5c5c5c
e8e8e8
e667a6
b2b2b2

Requirements
Must have
• One full colored side with a creative design and another with card info
• Use Color palette: #95C5C5 and/or #D38AA5
• Use fonts: Advent Pro
• Use website identity: https://www.glimora-example.com
Nice to have
• If needed extra font: Roboto

```html
<!DOCTYPE html>
<html lang="en">
<head>
<meta charset="utf-8">
<title>Glimora Business Card</title>
<link rel="stylesheet" href="https://fonts.googleapis.com/css2?family=Advent+Pro:wght@300;400;500&family=Open+Sans:wght@400;600&display=swap">
<style>
  :root {
    --backdrop: #e8e8e8;
    --pink: #e34297;
    --pink-soft: #e667a6;
    --rose: #d38aa5;
    --teal: #86cfc6;
    --teal-deep: #5fbfb4;
    --white: #ffffff;
    --ink: #2b2b2b;
    --grey: #5c5c5c;
    --grey-light: #b2b2b2;
  }
  * { box-sizing: border-box; margin: 0; padding: 0; }
  html, body {
    width: 1200px; height: 716px; overflow: hidden;
    background: var(--backdrop);
  }
  .canvas {
    width: 1200px; height: 716px;
    display: flex; align-items: center; justify-content: center; gap: 60px;
  }
  .card {
    position: relative; width: 500px; height: 286px;
    border-radius: 22px; overflow: hidden;
    box-shadow: 0 16px 36px rgba(0,0,0,.22);
  }

  /* Full-colour front */
  .card-front {
    background: linear-gradient(125deg, var(--pink) 0%, var(--pink-soft) 45%, var(--rose) 70%, var(--teal) 100%);
  }
  .card-front .accent-curve { position: absolute; inset: 0; }
  .card-front .brand { position: absolute; left: 70px; top: 98px; }
  .card-front .brand-dot { border-color: var(--white); }
  .card-front .brand-name { color: var(--white); }
  .website {
    position: absolute; left: 74px; top: 188px;
    font-family: "Open Sans", sans-serif; font-size: 14px;
    color: var(--white); letter-spacing: .3px;
  }

  .brand { display: flex; align-items: center; gap: 16px; }
  .brand-dot {
    width: 46px; height: 46px; border-radius: 50%;
    border: 2px solid var(--teal);
  }
  .brand-name {
    font-family: "Advent Pro", sans-serif; font-weight: 400;
    font-size: 48px; letter-spacing: 8px; text-transform: uppercase; line-height: 1;
  }

  /* Info back */
  .card-back { background: var(--ink); }
  .card-back .edge-band {
    position: absolute; left: 0; top: 0; bottom: 0; width: 10px;
    background: linear-gradient(180deg, var(--pink), var(--teal));
  }
  .card-back .brand { position: absolute; left: 40px; top: 58px; gap: 12px; }
  .card-back .brand-dot { width: 36px; height: 36px; border-color: var(--teal); }
  .card-back .brand-name { font-size: 36px; letter-spacing: 6px; color: var(--teal); }

  .details {
    position: absolute; left: 252px; top: 112px; width: 226px;
    font-family: "Open Sans", sans-serif; color: var(--white);
  }
  .person-name {
    font-family: "Advent Pro", sans-serif; font-weight: 500;
    font-size: 26px; line-height: 1.05;
  }
  .job-title { font-size: 13px; color: var(--pink-soft); margin: 2px 0 12px; }
  .contact-line {
    display: flex; align-items: flex-start; gap: 8px;
    font-size: 12px; line-height: 1.45; margin-bottom: 6px;
  }
  .contact-line svg { flex: none; margin-top: 3px; }

  .social {
    position: absolute; right: 40px; bottom: 24px;
    display: flex; gap: 30px;
  }
  .social-mark {
    width: 14px; height: 14px; border-radius: 3px; background: var(--teal);
  }
  .social-mark:nth-child(even) { background: var(--pink-soft); }
</style>
</head>
<body>
<main class="canvas">
  <section class="card card-front">
    <svg class="accent-curve" width="500" height="286" viewBox="0 0 500 286" aria-hidden="true">
      <path d="M0 236 C140 196 300 286 500 214 L500 286 L0 286 Z" fill="rgba(255,255,255,.14)"/>
      <path d="M0 260 C170 230 320 300 500 250 L500 286 L0 286 Z" fill="rgba(134,207,198,.35)"/>
    </svg>
    <div class="brand">
      <span class="brand-dot"></span>
      <span class="brand-name">Glimora</span>
    </div>
    <p class="website">www.glimora-example.com</p>
  </section>

  <section class="card card-back">
    <span class="edge-band"></span>
    <div class="brand">
      <span class="brand-dot"></span>
      <span class="brand-name">Glimora</span>
    </div>
    <div class="details">
      <p class="person-name">Your Name</p>
      <p class="job-title">Job Title</p>
      <p class="contact-line">
        <svg width="12" height="12" viewBox="0 0 24 24" aria-hidden="true"><path fill="var(--teal)" d="M6.6 10.8a15 15 0 0 0 6.6 6.6l2.2-2.2a1 1 0 0 1 1-.25 11.4 11.4 0 0 0 3.6.6 1 1 0 0 1 1 1V20a1 1 0 0 1-1 1A17 17 0 0 1 3 4a1 1 0 0 1 1-1h3.5a1 1 0 0 1 1 1c0 1.25.2 2.45.6 3.6a1 1 0 0 1-.25 1z"/></svg>
        <span>000 000 0000</span>
      </p>
      <p class="contact-line">
        <svg width="12" height="12" viewBox="0 0 24 24" aria-hidden="true"><path fill="var(--teal)" d="M12 2a7 7 0 0 0-7 7c0 5.25 7 13 7 13s7-7.75 7-13a7 7 0 0 0-7-7zm0 9.5A2.5 2.5 0 1 1 12 6.5a2.5 2.5 0 0 1 0 5z"/></svg>
        <span>1480 Lindenvale Ave, suite 310<br>Marisol Bay, Texas 70000</span>
      </p>
    </div>
    <div class="social">
      <span class="social-mark"></span>
      <span class="social-mark"></span>
      <span class="social-mark"></span>
      <span class="social-mark"></span>
    </div>
  </section>
</main>
</body>
</html>
```